Podcast Cover Art for rebranded podcast - I have inspiration for the designs

I've had a podcast ("Paperboat Radio Hour") since 2018, but I'm in the process of rebranding it. I've attached the old cover art below, which I loved, but I don't need it to look like that at all. The rebranded podcast is called 'Open Window with Marnie Cole.' I've included the show description at the bottom. I've been working on various design options in Canva, but not obsessed with anything yet, but I'm attaching the ones I do like that I think just need some refining. My very favorite is the one labeled 'favorite_Open Window' so I wouldn't mind keeping that general idea but perfected by a designer. Ultimately, I want something cool, fairly clean, modern, eye catching. I'm into neutrals with maybe a pop of color, so think black, white, grey..maybe silver, and I love a pop of red..and I'm not opposed to other options for the pop color. The show is going to be inspiring, entertaining, and funny. Oh and one other idea I had but I'm not sure if it makes sense with the title and/or what the show is about..but a vinyl record with Open Window with Marnie Cole on it somehow, on a record player..not sure.

Ever wonder what it means to truly live authentically? Curious about how to embrace the unpredictability of life? Ready for some heartfelt and lighthearted conversations that inspire and entertain?
Join Marnie Cole as she dives into the raw, real, and unscripted moments of life. In each episode, Marnie brings candid conversations and genuine insights into the ups and downs we all experience. From personal growth and self-discovery to inspiring stories and valuable life lessons, "Open Window" is a space where authenticity reigns and spontaneity is celebrated.
Whether she's sharing her own journey or chatting with inspiring guests, Marnie invites you to explore the beauty of living life without a script. Expect honest reflections, thought-provoking discussions, and a refreshing perspective on navigating life's unpredictable path—all with a dash of fun and humor to keep things lively and entertaining. Step into the unscripted moments of life and tune in for a blend of depth and lightheartedness that will leave you inspired, smiling, and most importantly laughing.

Target Market(s)

25-50 year old women and men (primarily women)

Font styles to use
Sans Serif

Requirements
Should not have
• nothing too feminine or girly, nothing cheesy :)

```html
<!DOCTYPE html>
<html lang="en">
<head>
<meta charset="utf-8">
<title>Open Window with Marnie Cole — Podcast Cover</title>
<link href="https://fonts.googleapis.com/css2?family=Oswald:wght@700&family=Montserrat:wght@800&display=swap" rel="stylesheet">
<style>
  :root {
    --ink: #000000;
    --glow: #3a3a3a;
    --slate: #5f5f5f;
    --paper: #ffffff;
    --snow: #f2f2f2;
    --signal: #e50914;
  }
  * { margin: 0; padding: 0; box-sizing: border-box; }
  html, body { width: 1200px; height: 1200px; overflow: hidden; background: var(--slate); }
  .cover {
    position: relative;
    width: 1200px;
    height: 1200px;
    overflow: hidden;
    background:
      radial-gradient(ellipse 420px 300px at 560px 760px, var(--glow) 0%, rgba(0,0,0,0) 100%),
      var(--ink);
  }
  .show-title {
    position: absolute;
    left: 180px;
    top: 80px;
    width: 640px;
    z-index: 2;
    font-family: "Oswald", sans-serif;
    font-weight: 700;
    color: var(--snow);
    text-transform: uppercase;
  }
  .show-title .line-main {
    display: block;
    font-size: 300px;
    line-height: 1;
    letter-spacing: -4px;
  }
  .show-title .line-sub {
    display: flex;
    align-items: center;
    gap: 22px;
    margin-top: 40px;
    font-size: 140px;
    line-height: 1;
    letter-spacing: -2px;
  }
  .show-title .marker {
    width: 90px;
    height: 90px;
    background: var(--signal);
    flex: none;
  }
  .torn-band {
    position: absolute;
    left: 0;
    top: 740px;
    width: 1200px;
    height: 460px;
  }
  .with-pill {
    position: absolute;
    left: 330px;
    top: 841px;
    width: 268px;
    height: 96px;
    border: 3px solid var(--signal);
    border-radius: 48px;
    display: flex;
    align-items: center;
    justify-content: center;
    font-family: "Montserrat", sans-serif;
    font-weight: 800;
    font-size: 62px;
    letter-spacing: 3px;
    color: var(--snow);
  }
  .host-name {
    position: absolute;
    left: 164px;
    top: 945px;
    width: 610px;
    text-align: center;
    font-family: "Oswald", sans-serif;
    font-weight: 700;
    font-size: 124px;
    line-height: 1.1;
    letter-spacing: -2px;
    color: var(--paper);
  }
  .host-name .surname { color: var(--ink); }
  .host-photo {
    position: absolute;
    left: 830px;
    top: 360px;
    width: 370px;
    height: 840px;
    border-radius: 185px 185px 0 0;
    background:
      radial-gradient(ellipse 120px 150px at 190px 200px, #9a9a9a 0%, rgba(0,0,0,0) 100%),
      linear-gradient(180deg, #2a2a2a 0%, #6b6b6b 45%, #bdbdbd 75%, #1a1a1a 100%);
  }
</style>
</head>
<body>
  <main class="cover">
    <h1 class="show-title">
      <span class="line-main">Open</span>
      <span class="line-sub"><span class="marker" aria-hidden="true"></span><span>Window</span></span>
    </h1>

    <svg class="torn-band" viewBox="0 0 1200 460" aria-hidden="true">
      <path fill="var(--paper)" d="M0 30 L40 22 L80 34 L130 20 L170 30 L210 24 L260 42 L300 30 L340 46 L380 36 L420 52 L455 38 L490 26 L520 36 L560 22 L600 0 L640 10 L680 4 L720 18 L760 30 L790 46 L820 44 L850 60 L880 70 L900 96 L900 460 L0 460 Z"/>
      <path fill="var(--slate)" d="M0 52 L35 44 L75 56 L120 44 L165 54 L210 48 L255 62 L300 54 L340 68 L385 58 L425 74 L460 62 L495 50 L525 58 L560 44 L600 26 L640 34 L680 30 L720 42 L760 54 L790 66 L820 68 L850 82 L880 92 L900 112 L900 460 L0 460 Z"/>
    </svg>

    <div class="with-pill">WITH</div>
    <p class="host-name">Marnie <span class="surname">Cole</span></p>

    <div class="host-photo" role="img" aria-label="Black and white photo of the host, smiling, with long dark hair and sunglasses on her head"></div>
  </main>
</body>
</html>
```